Lindqvar Foundation Letterhead

We are a newly established non profit registered in Maryland but operates in Africa, south of the sahara. We offer scholarships to deserving young adults from high school through college. Our color theme for our existing logo is purple, we want a design that is stylish, spellbinding yet a letterhead that projects seriousness. More information on www.thelindqvarfoundation.example

Target Market(s)

High school and college students in sub saharan African as well as our donors in the US

Industry/Entity Type

Non Profit

Font styles to use
Script

Requirements
Must have
• Logo at the top and if possible watermark the logo in the middle of the letterhead, contact address,
Should not have
• NA

```html
<!DOCTYPE html>
<html lang="en">
<head>
<meta charset="utf-8">
<title>Lindqvar Foundation Letterhead</title>
<link href="https://fonts.googleapis.com/css2?family=Cinzel:wght@400&family=Questrial&display=swap" rel="stylesheet">
<style>
  :root {
    --backdrop: #d4d3d6;
    --paper: #f6f6f6;
    --purple: #7a4fa3;
    --purple-soft: #8f73b6;
    --lavender: #aaa3cc;
    --ink: #5a5a5a;
    --watermark: #ebebeb;
    --strip: #dcdcdc;
  }
  * { margin: 0; padding: 0; box-sizing: border-box; }
  html, body {
    width: 1200px; height: 991px; overflow: hidden;
    background: var(--backdrop);
  }
  .letterhead {
    position: absolute; left: 312px; top: 89px;
    width: 577px; height: 813px;
    background: var(--paper);
    overflow: hidden;
  }
  .brand {
    position: absolute; left: 40px; top: 38px; width: 150px;
    text-align: center;
  }
  .brand-dot {
    display: block; margin: 0 auto 12px;
    width: 56px; height: 56px; border-radius: 50%;
    background: var(--purple);
  }
  .brand-name {
    font-family: "Cinzel", serif; font-size: 11px;
    color: var(--purple); letter-spacing: 0.2px; white-space: nowrap;
  }
  .contact {
    position: absolute; left: 408px; top: 58px;
    font-family: "Questrial", sans-serif; font-size: 8px; color: var(--ink);
    line-height: 10.5px; font-style: normal;
  }
  .contact-line { display: flex; align-items: center; gap: 5px; white-space: nowrap; }
  .contact-line svg { width: 7px; height: 7px; flex: none; }
  .address { margin-top: 6px; }
  .watermark {
    position: absolute; left: 100px; top: 301px; width: 372px; height: 372px;
  }
  .footer-wave { position: absolute; left: 0; bottom: 0; width: 577px; height: 40px; }
</style>
</head>
<body>
  <main class="letterhead">
    <header class="brand">
      <span class="brand-dot"></span>
      <div class="brand-name">Lindqvar Foundation Inc</div>
    </header>

    <address class="contact">
      <div class="contact-line">
        <svg viewBox="0 0 10 10"><rect width="10" height="10" rx="1.5" fill="#7a4fa3"/><path d="M3 2.2l1.2 1.6-.7.8c.5 1 1.2 1.7 2 2l.8-.7L7.9 7 7.2 8C4.8 7.8 2.2 5.2 2 2.8z" fill="#fff"/></svg>
        (555) 014-2287
      </div>
      <div class="contact-line">
        <svg viewBox="0 0 10 10"><rect width="10" height="10" rx="1.5" fill="#7a4fa3"/><rect x="2" y="3" width="6" height="4" fill="none" stroke="#fff" stroke-width=".8"/><path d="M2 3l3 2.2L8 3" fill="none" stroke="#fff" stroke-width=".8"/></svg>
        info@thelindqvarfoundation.example
      </div>
      <div class="contact-line">
        <svg viewBox="0 0 10 10"><rect width="10" height="10" rx="1.5" fill="#7a4fa3"/><circle cx="5" cy="5" r="2.8" fill="none" stroke="#fff" stroke-width=".7"/><path d="M2.2 5h5.6M5 2.2c-1.3 1.6-1.3 4 0 5.6M5 2.2c1.3 1.6 1.3 4 0 5.6" fill="none" stroke="#fff" stroke-width=".6"/></svg>
        www.thelindqvarfoundation.example
      </div>
      <div class="address">48 Meadowlark Rd - Suite 7<br>Harbourvale, ON Canada, K0X 2Z4</div>
    </address>

    <svg class="watermark" viewBox="0 0 372 372" aria-hidden="true">
      <circle cx="186" cy="186" r="180" fill="none" stroke="var(--watermark)" stroke-width="11"/>
    </svg>

    <svg class="footer-wave" viewBox="0 0 577 40" preserveAspectRatio="none" aria-hidden="true">
      <defs>
        <linearGradient id="bandGradient" x1="0" x2="1" y1="0" y2="0">
          <stop offset="0" stop-color="#6b3f94"/>
          <stop offset="0.55" stop-color="#aaa3cc"/>
          <stop offset="0.8" stop-color="#8a63ad"/>
          <stop offset="1" stop-color="#7a4fa3"/>
        </linearGradient>
      </defs>
      <path d="M0 16 C140 4 300 -4 420 2 C500 6 550 16 577 27 L577 40 L0 40Z" fill="var(--purple-soft)"/>
      <path d="M0 28 C150 14 320 6 440 8 C510 10 555 20 577 30 L577 40 L0 40Z" fill="var(--strip)"/>
      <path d="M180 40 C300 20 420 12 490 16 C530 19 560 28 577 35 L577 40Z" fill="url(#bandGradient)"/>
      <path d="M0 40 L0 30 C60 28 120 30 150 40Z" fill="var(--purple-soft)"/>
    </svg>
  </main>
</body>
</html>
```